Broschüre für Personaldienstleister
Zielgruppe
Wir sind ein Personaldienstleister und vermitteln ausländisches medizinisches Fachpersonal an deutsche Einrichtungen. Unsere Zielgruppe sind Krankenhäuser, Pflegeheime, Ärztehäuser, Praxen, Labore und weitere medizinische Institutionen.
Aufgabenstellung
Wir haben eine Infobroschüre sowie eine PowerPoint Präsentation bereits mit einem groben Design erstellt. Texte und Beispielbilder (Stockmaterial) sind ebenfalls vorhanden, gerne wünschen wir uns auch Eigeninitiative bei der Wahl der Bilder passend zum neuen Design.
Wir wünschen uns ein Redesign mit einem kreativen, einzigartigen Design. Zudem ist uns wichtig, dass unsere Infografiken qualitativ und hochwertig gestaltet werden.
Dieses Projekt ist mit zukünftigen Folgeprojekten verbunden, da wir weitere Präsentationen und Broschüren für andere Zielgruppen benötigen.

```html
<!DOCTYPE html>
<html lang="de">
<head>
<meta charset="utf-8">
<title>Velmora HR – Broschüre</title>
<link href="https://fonts.googleapis.com/css2?family=Roboto:wght@400;700;900&family=Varela+Round&display=swap" rel="stylesheet">
<style>
:root{
  --bg:#e4e6e6;
  --paper:#f6f7f7;
  --teal:#1f4b4b;
  --teal-dark:#173c3c;
  --sage:#b9d2c9;
  --sage-line:#6f8f86;
  --text:#3d4747;
  --muted:#6b7474;
  --accent:#2c7a57;
  --photo-a:#8aa9c4;
  --photo-b:#c9b7a0;
}
*{box-sizing:border-box;margin:0;padding:0}
html,body{width:1200px;height:901px;overflow:hidden;background:var(--bg)}
body{font-family:"Varela Round",Arial,sans-serif;color:var(--text);position:relative}
.spread{position:absolute;left:50px;top:62px;width:1100px;height:778px;display:flex;box-shadow:0 12px 30px rgba(0,0,0,.18)}
.page{position:relative;width:550px;height:778px;background:var(--paper);overflow:hidden}
.page--left{border-right:1px solid #d3d7d7}
.footer{position:absolute;left:0;right:0;bottom:0;height:30px;background:var(--teal);color:#fff;font-family:"Roboto",Arial,sans-serif;font-size:10.5px;display:flex;align-items:center;justify-content:space-around;letter-spacing:.3px}

/* left page */
.title{position:absolute;left:40px;top:40px;font-family:"Roboto",Arial,sans-serif;font-weight:900;font-size:34px;color:var(--teal);letter-spacing:.3px}
.steps{position:absolute;left:26px;top:108px;width:500px;display:grid;grid-template-columns:repeat(3,1fr);grid-auto-rows:150px;column-gap:8px}
.step{position:relative}
.rail{position:absolute;left:6px;top:20px;width:14px;height:100px;border-left:1.3px dashed var(--teal);border-top:1.3px dashed var(--teal);border-bottom:1.3px dashed var(--teal)}
.rail::before,.rail::after{content:"";position:absolute;right:-6px;width:9px;height:9px;border-radius:50%;background:var(--teal)}
.rail::before{top:-5px}
.rail::after{bottom:-5px}
.badge{position:absolute;left:32px;top:0;width:74px;height:74px;border-radius:50%;background:var(--sage);display:flex;align-items:center;justify-content:center}
.badge::after{content:"";position:absolute;inset:-9px;border-radius:50%;border:1.3px solid transparent;border-right-color:var(--teal);border-bottom-color:var(--teal);transform:rotate(-20deg)}
.badge svg{width:38px;height:38px;fill:none;stroke:var(--teal);stroke-width:2.2;stroke-linejoin:round;stroke-linecap:round}
.num{position:absolute;left:12px;top:92px;font-family:"Roboto",Arial,sans-serif;font-weight:700;font-size:17px;color:var(--teal)}
.step p{position:absolute;left:40px;top:82px;width:118px;font-size:6.3px;line-height:1.3;color:var(--muted)}

/* right page */
.photo{position:absolute;background:linear-gradient(135deg,var(--photo-b),var(--photo-a))}
.photo--staff{left:14px;top:22px;width:268px;height:290px}
.photo--care{left:300px;top:330px;width:236px;height:330px;background:linear-gradient(160deg,#e3e6ea,#9aa6c8 60%,#6c88b8)}
.pricing{position:absolute;left:298px;top:24px;width:236px}
.pricing h2{font-family:"Roboto",Arial,sans-serif;font-weight:700;font-size:15px;line-height:1.2;color:var(--teal);margin-bottom:10px}
.pricing p{font-size:8.6px;line-height:1.4;text-align:justify;margin-bottom:9px}
.talent{position:absolute;left:26px;top:340px;width:270px}
.talent h2{font-family:"Roboto",Arial,sans-serif;font-weight:900;font-size:20px;color:var(--teal);margin-bottom:8px}
.talent ul{list-style:none}
.talent li{position:relative;padding-left:18px;font-size:10px;line-height:1.52}
.talent li::before{content:"";position:absolute;left:2px;top:5px;width:6px;height:6px;border-radius:50%;background:var(--teal-dark)}
.talent .more{font-size:10px;color:var(--accent);margin-top:2px;padding-left:18px}
</style>
</head>
<body>
<div class="spread">
  <section class="page page--left">
    <h1 class="title">Unser Rekrutierungsverfahren</h1>
    <div class="steps">
      <div class="step"><div class="rail"></div>
        <div class="badge"><svg viewBox="0 0 40 40"><rect x="8" y="6" width="22" height="28" rx="2"/><path d="M13 13h12M13 19h12M13 25h7M26 30l8-10"/></svg></div>
        <span class="num">01</span><p>Bewerber:in wird auf uns aufmerksam, füllt unser Bewerbungsformular aus und reicht die nötigen Dokumente ein.</p></div>
      <div class="step"><div class="rail"></div>
        <div class="badge"><svg viewBox="0 0 40 40"><path d="M5 8h24v15H14l-6 5v-5H5z"/><path d="M29 14h6v14h-3v4l-5-4h-9v-5"/><text x="10" y="19" font-size="8" fill="#1f4b4b" stroke="none" font-family="Roboto">DE</text></svg></div>
        <span class="num">02</span><p>Um das erforderliche Sprachniveau B2 zu erreichen, bieten wir Bewerber:innen kostenlose interne Sprachkurse an.</p></div>
      <div class="step"><div class="rail"></div>
        <div class="badge"><svg viewBox="0 0 40 40"><path d="M8 10h14l6 6v18H8z"/><path d="M14 6h14l6 6v16"/></svg></div>
        <span class="num">03</span><p>Parallel zu ihren sprachlichen Vorbereitungen beginnen die Bewerber:innen mit dem Anerkennungsprozess.</p></div>
      <div class="step"><div class="rail"></div>
        <div class="badge" role="img" aria-label="Symbol: Hände, die Kandidat:innen tragen"></div>
        <span class="num">04</span><p>Wir bereiten unsere Kandidat:innen auf die bevorstehenden Videointerviews vor und erarbeiten proaktive Lösungen für Situationen, die während des Vorstellungsgesprächs auftreten können.</p></div>
      <div class="step"><div class="rail"></div>
        <div class="badge" role="img" aria-label="Symbol: Vorstellungsgespräch am Tisch"></div>
        <span class="num">05</span><p>Die Bewerber:innen haben Vorstellungsgespräche mit potenziellen Arbeitgebern aus Deutschland. Wir begleiten Sie dabei.</p></div>
      <div class="step"><div class="rail"></div>
        <div class="badge"><svg viewBox="0 0 40 40"><rect x="6" y="12" width="22" height="22"/><rect x="11" y="6" width="23" height="22"/><path d="M16 13h13M16 18h13M16 23h8"/></svg></div>
        <span class="num">06</span><p>Bei erfolgreicher Einigung kommt es zur Unterzeichnung eines Arbeitsvertrags. Wir kümmern uns um die weiteren Prozessabläufe.</p></div>
      <div class="step"><div class="rail"></div>
        <div class="badge"><svg viewBox="0 0 40 40"><path d="M5 20L20 7l15 13M9 17v16h22V17"/><rect x="16" y="24" width="8" height="9"/><rect x="13" y="18" width="14" height="4"/></svg></div>
        <span class="num">07</span><p>Die für die Beschäftigung in Deutschland erforderlichen Dokumente werden von uns erstellt bzw. eingeholt und wir suchen eine Unterkunft in der Nähe des künftigen Arbeitsortes.</p></div>
      <div class="step"><div class="rail"></div>
        <div class="badge" role="img" aria-label="Symbol: Reisende Person mit Koffer"></div>
        <span class="num">08</span><p>Einreise Ihres/r neuen Mitarbeiter:in nach Deutschland. Wir organisieren die Abholung vom Flughafen und den Transport zur Unterkunft.</p></div>
      <div class="step"><div class="rail"></div>
        <div class="badge" role="img" aria-label="Symbol: Pflegefachkraft"></div>
        <span class="num">09</span><p>Wir bereiten Ihre neue Fachkraft auf den Arbeitsantritt vor und begleiten sie zum ersten Arbeitstag.</p></div>
      <div class="step"><div class="rail"></div>
        <div class="badge"><svg viewBox="0 0 40 40"><path d="M7 7h10v4a3 3 0 1 0 4 0V7h12v11h-4a3 3 0 1 0 0 4h4v11H21v-4a3 3 0 1 0-4 0v4H7V22h4a3 3 0 1 0 0-4H7z"/></svg></div>
        <span class="num">10</span><p>Unsere Kandidat:innen werden während der gesamten Probe-/Einarbeitungszeit von uns unterstützt und betreut.</p></div>
    </div>
    <footer class="footer"><span>+49 000 555 12 340</span><span>hr@velmora.com</span><span>www.velmora-hr.com</span></footer>
  </section>

  <section class="page page--right">
    <div class="photo photo--staff" role="img" aria-label="Foto: zwei Pflegekräfte in blauer Kleidung am Fenster"></div>
    <div class="pricing">
      <h2>Was kostet eine gute und faire Rekrutierung bei uns?</h2>
      <p>Wir bei Velmora HR legen großen Wert auf Kundenzufriedenheit. Mit unserem 360°-Service decken wir alle wichtigen Serviceleistungen rund um die Rekrutierung von ausländischen Fachkräften ab und bieten Ihnen dadurch noch mehr Flexibilität und Dynamik.</p>
      <p>Bei der Berechnung unserer Preise spielen somit viele Faktoren eine wichtige Rolle und sind stark abhängig vom Leistungsumfang und der Art der Rekrutierung.</p>
      <p>Preisangebote kalkulieren wir individuell und bedarfsgerecht erst mit einer konkreten und detaillierten Nachfrage.</p>
      <p>Teilen Sie uns jetzt Ihren Personalbedarf mit!</p>
    </div>
    <div class="talent">
      <h2>Unser Talentpool</h2>
      <ul>
        <li>Gesundheits- und Krankenpfleger:in</li>
        <li>Pflegefachmann /-frau</li>
        <li>Pflegefachassistent:in</li>
        <li>Altenpfleger:in</li>
        <li>Arzt/Ärztin</li>
        <li>Hebamme</li>
        <li>Anästhesietechnische:r Assistent:in (ATA)</li>
        <li>Operationstechnische:r Assistent:in (OTA)</li>
        <li>Medizinisch-technische:r Laborassistent:in (MTLA)</li>
        <li>Medizinisch-technische:r Radiologieassistentin (MTRA)</li>
        <li>Pflegehilfskräfte</li>
        <li>Pflegefachassistent:in</li>
        <li>Notfallsanitäter:in</li>
        <li>Rettungssanitäter:in</li>
        <li>Physiotherapeut:innen</li>
      </ul>
      <p class="more">… und viele weitere medizinische Berufe.</p>
    </div>
    <div class="photo photo--care" role="img" aria-label="Foto: Pflegekraft mit Maske betreut eine Patientin"></div>
    <footer class="footer"><span>+49 000 555 12 340</span><span>hr@velmora.com</span><span>www.velmora-hr.com</span></footer>
  </section>
</div>
</body>
</html>
```